Communication and Marketing agency needs a new presentation card

We are a group of communication and marketing agencies specialized in companies that are in the logistics and industrial sector. The head agency is TELVANO Grupo and the group consists of 4 agencies: TELVANO Media, TELVANO Digital, TELVANO Research and DifundeEnPantalla. We hace 4 offices in Spain (Madrid, Barcelona, Valencia and Murcia). We are looking for a clean and attractive design that transmits our experience, brand presence in the market and knowledge to those who receive the card.It has to maintain the colors of the logo that is attached.
Target Market(s)
logistics and industrial sector
Marketing department
Contact Information for Business Card
Clean and attractive design

```html
<!DOCTYPE html>
<html lang="en">
<head>
<meta charset="utf-8">
<title>TELVANO Grupo – Business Card</title>
<link rel="stylesheet" href="https://fonts.googleapis.com/css2?family=Open+Sans:wght@400;600&family=Oswald:wght@600&display=swap">
<style>
  :root {
    --bg: #2b2b2d;
    --card: #1d1d1f;
    --red: #d9433a;
    --silver: #d8d8d8;
    --white: #f4f4f4;
    --grey: #c9c9c9;
  }
  * { margin: 0; padding: 0; box-sizing: border-box; }
  html, body { width: 1200px; height: 900px; overflow: hidden; }
  body {
    background: var(--bg);
    font-family: "Open Sans", sans-serif;
    display: flex;
    flex-direction: column;
    align-items: center;
    justify-content: center;
    gap: 40px;
  }
  .card {
    width: 620px;
    height: 354px;
    background: var(--card);
    position: relative;
    box-shadow: 0 10px 30px rgba(0,0,0,.45);
  }
  /* Front */
  .card--front {
    display: flex;
    align-items: center;
    justify-content: center;
  }
  .brand-name {
    font-family: "Open Sans", sans-serif;
    font-weight: 600;
    font-size: 44px;
    letter-spacing: 3px;
    color: var(--silver);
    white-space: nowrap;
  }
  /* Back */
  .card--back {
    border-bottom: 6px solid var(--red);
  }
  .back-logo {
    position: absolute;
    left: 38px;
    top: 118px;
    width: 240px;
    text-align: right;
  }
  .back-logo .brand-name {
    font-size: 30px;
    letter-spacing: 2px;
    color: var(--red);
  }
  .divider {
    position: absolute;
    left: 300px;
    top: 96px;
    width: 2px;
    height: 128px;
    background: var(--red);
  }
  .contact {
    position: absolute;
    left: 328px;
    top: 94px;
  }
  .person-name {
    font-family: "Oswald", sans-serif;
    font-weight: 600;
    font-size: 34px;
    letter-spacing: 2px;
    color: var(--white);
    line-height: 1;
  }
  .person-role {
    font-size: 15px;
    font-weight: 600;
    color: var(--red);
    letter-spacing: 1px;
    margin: 4px 0 12px;
  }
  .contact-list { list-style: none; }
  .contact-list li {
    display: flex;
    align-items: center;
    gap: 12px;
    font-size: 15px;
    color: var(--grey);
    line-height: 24px;
  }
  .contact-list svg { width: 13px; height: 13px; flex: none; }
  .accent { color: var(--red); }
  .address {
    position: absolute;
    left: 170px;
    bottom: 26px;
    font-size: 14px;
    color: var(--grey);
  }
</style>
</head>
<body>

  <section class="card card--front">
    <p class="brand-name">TELVANO Grupo</p>
  </section>

  <section class="card card--back">
    <div class="back-logo">
      <p class="brand-name">TELVANO Grupo</p>
    </div>
    <div class="divider"></div>
    <div class="contact">
      <h1 class="person-name">MARCO RUIZ</h1>
      <p class="person-role">CEO &amp; FOUNDER</p>
      <ul class="contact-list">
        <li>
          <svg viewBox="0 0 12 16" aria-hidden="true"><rect x="1" y="1" width="10" height="14" rx="1.5" fill="none" stroke="#d9433a" stroke-width="1.6"/><circle cx="6" cy="12.3" r="0.9" fill="#d9433a"/></svg>
          000 111 222 3333
        </li>
        <li>
          <svg viewBox="0 0 16 12" aria-hidden="true"><rect x="0" y="0" width="16" height="12" rx="1" fill="#d9433a"/><path d="M0.5 1 L8 7 L15.5 1" fill="none" stroke="#1d1d1f" stroke-width="1.4"/></svg>
          urname@email.com
        </li>
        <li>
          <svg viewBox="0 0 16 16" aria-hidden="true"><circle cx="9" cy="7" r="5.5" fill="none" stroke="#d9433a" stroke-width="1.8"/><path d="M5 11 L1 15" stroke="#d9433a" stroke-width="2"/></svg>
          <span>www.<span class="accent">ursitename</span>.com</span>
        </li>
      </ul>
    </div>
    <p class="address"><span class="accent">Address :</span> Your Street Address, NewYork City 1234</p>
  </section>

</body>
</html>
```